QVR business card

Need a business card for a company that provides instructional design and elearning development services. The website is here: http://quorvane.studio/

I'm attaching a current logo, as well as the old business card design. While I like to keep it clean, the old design is too simplistic for my liking. The only idea I want to reuse from the old design is placing industry jargon on the back of the card, just need a better way to present it. But if you have other ideas for the back--feel free to experiment.

Please use the colors complementary to the color we have on the website. Thank you!

```html
<!DOCTYPE html>
<html lang="en">
<head>
<meta charset="utf-8">
<title>QVR business card</title>
<link rel="stylesheet" href="https://fonts.googleapis.com/css2?family=Jost:wght@600&family=Oswald:wght@700&family=Varela+Round&family=Roboto:wght@400&display=swap">
<style>
  :root {
    --backdrop: #b4b2b2;
    --card: #2d2d2f;
    --card-pattern: #333336;
    --teal: #1fb39f;
    --gold: #dcd48e;
    --white: #ffffff;
    --name-grey: #b9b9b9;
    --detail-grey: #c4c4c4;
  }
  * { margin: 0; padding: 0; box-sizing: border-box; }
  html, body { width: 1200px; height: 1200px; overflow: hidden; }
  body { background: var(--backdrop); position: relative; }

  .card {
    position: absolute;
    background: var(--card);
    border-radius: 18px;
    overflow: hidden;
  }
  .card--front { left: 238px; top: 118px; width: 712px; height: 419px; }
  .card--back  { left: 232px; top: 645px; width: 708px; height: 417px; }

  .card__texture {
    position: absolute; inset: 0;
    background: radial-gradient(circle at 50% 50%, var(--card-pattern), var(--card) 80%);
  }

  .jargon {
    position: absolute;
    left: 42px;
    width: 630px;
    font-family: "Jost", sans-serif;
    font-weight: 600;
    font-size: 41px;
    line-height: 53.5px;
    color: var(--teal);
    text-transform: uppercase;
    text-align: justify;
    text-align-last: justify;
    letter-spacing: 2px;
  }
  .jargon--top { top: 18px; }
  .jargon--bottom { top: 243px; }

  .help-band {
    position: absolute;
    left: 0; right: 0; top: 180px;
    height: 60px;
    display: flex;
    align-items: center;
    justify-content: space-between;
  }
  .help-band__bar { width: 24px; height: 40px; background: var(--white); }
  .help-band__bar--right { width: 22px; }
  .help-band__text {
    font-family: "Oswald", sans-serif;
    font-weight: 700;
    font-size: 74px;
    line-height: 1;
    color: var(--white);
    letter-spacing: -3px;
    transform: scaleX(0.93);
  }

  .brand {
    position: absolute;
    left: 60px; top: 58px;
    display: flex; align-items: center; gap: 14px;
  }
  .brand__mark { width: 34px; height: 34px; background: var(--teal); border-radius: 50%; }
  .brand__name {
    font-family: "Varela Round", sans-serif;
    font-size: 46px;
    color: var(--gold);
    letter-spacing: 2px;
  }

  .contact {
    position: absolute;
    left: 334px; top: 222px;
    font-family: "Roboto", sans-serif;
  }
  .contact__name {
    font-family: "Varela Round", sans-serif;
    font-size: 22px;
    color: var(--name-grey);
    margin-bottom: 24px;
    letter-spacing: 0.5px;
  }
  .contact__list { list-style: none; }
  .contact__item {
    display: flex; align-items: center; gap: 20px;
    font-size: 17px;
    color: var(--detail-grey);
    height: 27.5px;
  }
  .contact__icon { width: 15px; height: 15px; flex: none; }

  .stripe { position: absolute; left: 0; bottom: 0; width: 708px; height: 20px; }
</style>
</head>
<body>

  <section class="card card--front" aria-label="Card back with industry terms">
    <div class="card__texture" role="img" aria-label="Faint gear pattern over dark charcoal"></div>
    <div class="jargon jargon--top">
      <p>Mobile Learning SCORM</p>
      <p>Instructional Design LMS</p>
      <p>MOOCs eLearning HTML5</p>
    </div>
    <div class="help-band">
      <span class="help-band__bar"></span>
      <span class="help-band__text">HOW CAN WE HELP?</span>
      <span class="help-band__bar help-band__bar--right"></span>
    </div>
    <div class="jargon jargon--bottom">
      <p>Adult Learning Theory</p>
      <p>Gamification Classroom</p>
      <p>xAPI Blended Learning</p>
    </div>
  </section>

  <section class="card card--back" aria-label="Card front with contact details">
    <div class="brand">
      <span class="brand__mark"></span>
      <span class="brand__name">QVR</span>
    </div>

    <div class="contact">
      <p class="contact__name">Marek Halloway</p>
      <ul class="contact__list">
        <li class="contact__item">
          <svg class="contact__icon" viewBox="0 0 16 16" aria-hidden="true">
            <path d="M1 5 Q8 0 15 5 L13 7 L11 5.5 L5 5.5 L3 7 Z" fill="var(--teal)"/>
            <rect x="3" y="8" width="10" height="6" rx="1" fill="var(--teal)"/>
          </svg>
          555-014-2290
        </li>
        <li class="contact__item">
          <svg class="contact__icon" viewBox="0 0 16 16" aria-hidden="true" fill="none" stroke="var(--teal)" stroke-width="1.5">
            <circle cx="8" cy="8" r="6.5"/>
            <ellipse cx="8" cy="8" rx="3" ry="6.5"/>
            <line x1="1.5" y1="8" x2="14.5" y2="8"/>
          </svg>
          www.quorvane.studio
        </li>
        <li class="contact__item">
          <svg class="contact__icon" viewBox="0 0 16 16" aria-hidden="true">
            <rect x="1" y="3" width="14" height="10" fill="var(--teal)"/>
            <path d="M1 3 L8 9 L15 3" fill="none" stroke="var(--card)" stroke-width="1.4"/>
          </svg>
          mhalloway@quorvane.studio
        </li>
      </ul>
    </div>

    <svg class="stripe" viewBox="0 0 708 20" preserveAspectRatio="none" aria-hidden="true">
      <polygon points="0,0 500,0 460,20 0,20" fill="var(--teal)"/>
      <polygon points="500,0 708,0 708,20 460,20" fill="var(--gold)"/>
    </svg>
  </section>

</body>
</html>
```